Request for Business Card Design

Hi. My name is Marlene, I am looking for a new business card design for my company, Quarrow Signal Instruments, LLC. I really like the design you did for Tarsel Venture and was hoping you could do something similar using our full logo and our mark. I am also open to any raised texture design using our mark. I have attached our full logo, which would need to be somewhere on the card, as well as the mark in both outline and full form, as well as our brand colors / guide. The card does not have to be white, as long as our logo and mark appear. I actually like darker colored business cards more, but am open to all options. If you are interested in working with me, please let me know. We would also take the business card design into letterhead design if you can do that.

```html
<!DOCTYPE html>
<html lang="en">
<head>
<meta charset="utf-8">
<title>Quarrow Signal Instruments — Business Card</title>
<link href="https://fonts.googleapis.com/css2?family=Barlow:wght@400;500;700&family=Open+Sans:wght@400;700&display=swap" rel="stylesheet">
<style>
  :root {
    --backdrop: #1f1f20;
    --card-light: #505053;
    --card-dark: #2f2f31;
    --ink: #ffffff;
    --ink-soft: #e4e4e6;
  }
  * { margin: 0; padding: 0; box-sizing: border-box; }
  html, body { width: 1200px; height: 1200px; overflow: hidden; }
  body { background: var(--backdrop); position: relative; font-family: "Barlow", sans-serif; color: var(--ink); }

  .card {
    position: absolute;
    width: 700px; height: 400px;
    background: radial-gradient(ellipse at 50% 40%, var(--card-light) 0%, var(--card-dark) 85%);
    box-shadow: 0 14px 30px rgba(0,0,0,.5);
  }
  .card--front { left: 420px; top: 150px; }
  .card--back  { left: 80px;  top: 640px; }

  .logo { position: absolute; display: flex; align-items: center; gap: 18px; }
  .logo__dot { width: 62px; height: 62px; border-radius: 50%; background: var(--ink); flex: none; }
  .logo__text { font-family: "Barlow", sans-serif; font-weight: 700; color: var(--ink); line-height: 1; }
  .logo__name { display: block; font-size: 66px; letter-spacing: 5px; }
  .logo__sub  { display: block; font-size: 18px; letter-spacing: 1.2px; margin-top: 6px; }

  .card--front .logo { left: 150px; top: 130px; }
  .card--back  .logo { left: 250px; top: 70px; }
  .card--back  .logo__dot { width: 52px; height: 52px; }
  .card--back  .logo__name { font-size: 56px; letter-spacing: 4px; }
  .card--back  .logo__sub { font-size: 15px; }

  .social { position: absolute; right: 50px; bottom: 44px; display: flex; gap: 26px; }
  .social__box { width: 34px; height: 34px; border: 3px solid var(--ink); border-radius: 5px; }
  .social__box--solid { background: var(--ink); }

  .person { position: absolute; left: 80px; top: 190px; }
  .person__name { font-family: "Open Sans", sans-serif; font-weight: 700; font-size: 22px; color: var(--ink-soft); }
  .person__role { font-family: "Open Sans", sans-serif; font-size: 15px; color: var(--ink-soft); margin-top: 2px; }

  .address { position: absolute; left: 330px; top: 205px; font-size: 19px; line-height: 1.2; color: var(--ink-soft); }
  .contact { position: absolute; left: 300px; top: 262px; list-style: none; font-size: 19px; line-height: 1.35; color: var(--ink-soft); }
  .contact li { display: flex; align-items: center; gap: 10px; }
  .contact svg { width: 15px; height: 15px; fill: var(--ink-soft); flex: none; }
</style>
</head>
<body>

<section class="card card--front" aria-label="Card front">
  <div class="logo">
    <span class="logo__dot"></span>
    <span class="logo__text">
      <span class="logo__name">QUARROW</span>
      <span class="logo__sub">SIGNAL INSTRUMENTS</span>
    </span>
  </div>
  <div class="social" aria-label="Social profiles">
    <span class="social__box social__box--solid"></span>
    <span class="social__box"></span>
  </div>
</section>

<section class="card card--back" aria-label="Card back">
  <div class="logo">
    <span class="logo__dot"></span>
    <span class="logo__text">
      <span class="logo__name">QUARROW</span>
      <span class="logo__sub">SIGNAL INSTRUMENTS</span>
    </span>
  </div>

  <div class="person">
    <p class="person__name">Marlene</p>
    <p class="person__role">Founder &amp; Director</p>
  </div>

  <p class="address">1180 Harlow Ridge Drive.<br>Fenwick, CO 80417</p>

  <ul class="contact">
    <li>
      <svg viewBox="0 0 16 16" aria-hidden="true"><path d="M3 1h3l1.5 4-2 1.2a9 9 0 0 0 4.3 4.3L11 8.5l4 1.5v3a2 2 0 0 1-2 2A12 12 0 0 1 1 3a2 2 0 0 1 2-2z"/></svg>
      +001 303 555 0142
    </li>
    <li>
      <svg viewBox="0 0 16 16" aria-hidden="true"><path d="M4 1h8v4H4z"/><path d="M1 6h14v6h-3v3H4v-3H1zM5 10v4h6v-4z"/></svg>
      +001 303 555 0187
    </li>
    <li>
      <svg viewBox="0 0 16 16" aria-hidden="true"><path d="M1 3h14v10H1zM2.5 4.5 8 9l5.5-4.5"/><path d="M1 3h14L8 8.5z" fill="#3a3a3c"/></svg>
      info@quarrowsignal.com
    </li>
    <li>
      <svg viewBox="0 0 16 16" aria-hidden="true"><circle cx="8" cy="8" r="7"/><path d="M1 7.3h14v1.4H1zM7.3 1h1.4v14H7.3z" fill="#3a3a3c"/></svg>
      www.quarrowsignal.com
    </li>
  </ul>
</section>

</body>
</html>
```